New eyelid plastic surgery office needs a business card design-Eyelid Care Partners of the Brenton

I recently used PixelForge for my logo design and was very pleased with creativity and results. It was a difficult decision for me. Now I would like to create a business card based on this logo, which I will attach.

The text should be easily legible as some of my patients have difficulty seeing, but I would like a subtle, sophisticated artistry also evident to make the card memorable. Would like the card based on a similar color scheme as the logo but the inverse or other complementary colors may prove interesting
Updates

A good question was asked...my concern about my visually impaired patients was really my desire to avoid italicized or calligraphic type fonts that may be hard to read. Standard font size for a business card would be fine. Thanks!

Thank you so much for the great work so far. I wanted to give you my particular contact information to see if that would change the look of the cards. Martin Delacourt, MD Address: 2718 Harborview Lane, Suite 206 Wilmington, NC 28517 Phone: 910-555-0193 Fax: 910-555-0194 Website: www.brentonlidstudio.example Please delete the email slot from the card. Thanks so much!

Industry/Entity Type

Plastic

```html
<!DOCTYPE html>
<html lang="en">
<head>
<meta charset="utf-8">
<title>Eyelid Care Partners of the Brenton — Business Card</title>
<link rel="stylesheet" href="https://fonts.googleapis.com/css2?family=Mulish:wght@400;700&display=swap">
<style>
  :root {
    --canvas: #e7e7e9;
    --card: #f4f4f5;
    --brand-blue: #2f4fa3;
    --band-grey: #d3d4d7;
    --ink: #3a3a3c;
    --ink-soft: #555558;
    --accent-text: #3b5cb0;
  }
  * { margin: 0; padding: 0; box-sizing: border-box; }
  html, body { width: 1200px; height: 900px; overflow: hidden; }
  body {
    background: var(--canvas);
    font-family: "Mulish", sans-serif;
    display: flex;
    flex-direction: column;
    align-items: center;
    justify-content: center;
    gap: 52px;
  }
  .card {
    position: relative;
    width: 630px;
    height: 360px;
    background: var(--card);
    box-shadow: 0 6px 18px rgba(0,0,0,0.12);
    overflow: hidden;
  }

  /* Practice name, set in the card's text font */
  .practice-name {
    font-family: "Mulish", sans-serif;
    font-weight: 700;
    color: var(--ink);
    white-space: nowrap;
    letter-spacing: 0.04em;
  }
  .card-front .practice-name {
    position: absolute;
    top: 164px;
    left: 0;
    width: 100%;
    text-align: center;
    font-size: 24px;
  }
  .card-back .practice-name {
    position: absolute;
    top: 62px;
    left: 250px;
    font-size: 15px;
  }

  .holder {
    position: absolute;
    top: 106px;
    left: 40px;
  }
  .holder-name {
    font-weight: 700;
    font-size: 17px;
    letter-spacing: 0.12em;
    color: var(--ink);
  }
  .holder-role {
    margin-top: 6px;
    font-size: 11px;
    letter-spacing: 0.12em;
    color: var(--accent-text);
  }

  .contact {
    position: absolute;
    top: 172px;
    left: 300px;
    list-style: none;
    font-size: 13px;
    letter-spacing: 0.1em;
    color: var(--ink-soft);
  }
  .contact li {
    display: flex;
    align-items: center;
    height: 26px;
    white-space: nowrap;
  }
  .contact .icon {
    width: 14px;
    height: 14px;
    margin-left: -26px;
    margin-right: 12px;
    fill: none;
    stroke: var(--brand-blue);
    stroke-width: 1.6;
  }
  .contact .location { margin-bottom: 4px; }

  .edge-band {
    position: absolute;
    left: 0;
    bottom: 0;
    width: 100%;
    height: 120px;
  }
</style>
</head>
<body>

  <section class="card card-front" aria-label="Card front">
    <p class="practice-name">Eyelid Care Partners of the Brenton</p>
  </section>

  <section class="card card-back" aria-label="Card back">
    <svg class="edge-band" viewBox="0 0 630 120" preserveAspectRatio="none" aria-hidden="true">
      <path d="M0 20 C 40 70, 90 96, 170 100 L 630 100 L 630 120 L 0 120 Z" fill="var(--band-grey)"/>
      <path d="M0 62 C 50 96, 110 108, 190 108 L 630 108 L 630 120 L 0 120 Z" fill="var(--brand-blue)"/>
    </svg>

    <div class="holder">
      <p class="holder-name">Elena Marsh Vadley</p>
      <p class="holder-role">Director of Operations</p>
    </div>

    <p class="practice-name">Eyelid Care Partners of the Brenton</p>

    <ul class="contact">
      <li class="location">Washington DC | New York</li>
      <li>
        <svg class="icon" viewBox="0 0 16 16" aria-hidden="true"><path d="M4 2 L6.5 2 L7.5 5 L6 6.3 C6.8 8 8 9.2 9.7 10 L11 8.5 L14 9.5 L14 12 C14 13 13 14 12 14 C6.5 13.5 2.5 9.5 2 4 C2 3 3 2 4 2 Z"/></svg>
        301-555-0148
      </li>
      <li>
        <svg class="icon" viewBox="0 0 16 16" aria-hidden="true"><rect x="1.5" y="3.5" width="13" height="9"/><path d="M1.5 3.5 L8 9 L14.5 3.5"/></svg>
        emvadley@brentonlidstudio.example
      </li>
      <li>
        <svg class="icon" viewBox="0 0 16 16" aria-hidden="true"><circle cx="8" cy="8" r="6.2"/><ellipse cx="8" cy="8" rx="2.8" ry="6.2"/><path d="M1.8 8 H14.2"/></svg>
        www.brentonlidstudio.example
      </li>
    </ul>
  </section>

</body>
</html>
```